One piece Trade show banner, 8' x 8' square

One piece banner for trade show
8' x 8' airborne geophysical company

Target Market(s)

Business

Industry/Entity Type

mineral exploration and science

Colors
0054AA
0677BA
7BADD7
CADEEF
E8F1F8
FFC000
F8CF3A
FAE287
FDF2CF
FEFAEE

Requirements
Must have
• Company logo (attached), slogan (Airborne Geophysics for Discovery). We are looking for a new banner, for a standard 8 x 8' square one-piece booth. I have attached some pictures, our logo, our old banner for reference, and two examples from unrelated companies from a tradeshow that we like. If its possible I'd like to change the color of the helicopter from green to dark grey. IE, keep the orange and white, just change green to dark grey. Looking for a simple, clean design with minimal text.
Nice to have
• I have attached examples of banners that we like (2xIMG), plus our old 3-piece banner r.
Should not have
• Green in the helicopter. Please change the color of the helicopter with green/orange/white to dark grey/orange/white. IE change the green to dark grey and leave the orange and white alone. I've attached lots of pictures but I don't expect them all to be used.

```html
<!DOCTYPE html>
<html lang="en">
<head>
<meta charset="UTF-8">
<title>Altair Geosurveys – Trade Show Banner</title>
<link rel="stylesheet" href="https://fonts.googleapis.com/css2?family=Poppins:wght@400;600;700;800&display=swap">
<style>
  :root {
    --bg: #1b1b1b;
    --gold: #ffc000;
    --blue-deep: #0054aa;
    --blue-mid: #0677ba;
    --blue-light: #7badd7;
    --blue-pale: #cadeef;
    --white: #ffffff;
    --ink: #1b1b1b;
  }
  * { margin: 0; padding: 0; box-sizing: border-box; }
  html, body { width: 1200px; height: 1200px; overflow: hidden; background: var(--bg); }
  .banner {
    position: relative;
    width: 1200px;
    height: 1200px;
    background: var(--bg);
    font-family: "Poppins", sans-serif;
    color: var(--white);
    overflow: hidden;
  }

  /* Brand mark */
  .brand {
    position: absolute;
    left: 20px; top: 19px;
    width: 241px; height: 316px;
    display: flex;
    flex-direction: column;
    align-items: center;
    justify-content: center;
    gap: 14px;
  }
  .brand-dot {
    width: 58px; height: 58px;
    border-radius: 50%;
    background: var(--blue-mid);
  }
  .brand-name {
    font-weight: 700;
    font-size: 30px;
    line-height: 1.15;
    text-align: center;
    color: var(--white);
  }

  /* Headline */
  .headline {
    position: absolute;
    left: 290px; top: 42px;
    width: 860px;
    text-align: center;
    color: var(--gold);
    font-weight: 700;
    font-size: 102px;
    line-height: 108px;
    letter-spacing: -0.5px;
  }

  /* Photo frames */
  .photo {
    position: absolute;
    border: 4px solid var(--gold);
  }
  .photo-snow   { left: 34px;  top: 366px; width: 339px; height: 302px;
                  background: linear-gradient(160deg, #2a2f33, #4a5560 55%, #1e2226); }
  .photo-valley { left: 428px; top: 371px; width: 336px; height: 297px;
                  background: linear-gradient(180deg, #e9edf0 0%, #b9c4cc 45%, #7fa36a 70%, #5d8a45 100%); }
  .photo-lake   { left: 821px; top: 371px; width: 337px; height: 297px;
                  background: linear-gradient(180deg, #8c8a84 0%, #a9a39a 30%, #3ab0c6 50%, #1f9bb6 100%); }
  .photo-sky    { left: 37px;  top: 680px; width: 1109px; height: 245px;
                  background: linear-gradient(90deg, #0c4fd0, #1a6ae0 60%, #0b50c8); }

  /* Ribbons */
  .ribbon {
    position: absolute;
    top: 943px;
    height: 56px;
    background: var(--blue-deep);
    font-weight: 700;
    font-size: 33px;
    line-height: 56px;
    color: var(--white);
  }
  .ribbon-local  { left: 24px;  width: 302px; padding-left: 6px;
                   clip-path: polygon(0 0, 100% 0, 94% 100%, 0 100%); }
  .ribbon-global { left: 868px; width: 315px; padding-left: 4px;
                   clip-path: polygon(0 0, 100% 0, 94% 100%, 0 100%); }

  /* Services */
  .service {
    position: absolute;
    top: 1020px;
  }
  .service-title {
    color: var(--gold);
    font-weight: 600;
    font-size: 29px;
    line-height: 34px;
  }
  .service-list {
    list-style: none;
    font-weight: 400;
    font-size: 21px;
    line-height: 25.5px;
  }
  .service-em       { left: 30px; }
  .service-em .service-list { padding-left: 2px; }
  .service-radio    { left: 340px; }
  .service-mag      { left: 584px; }
  .service-consult  { left: 997px; }

  /* Footer */
  .footer {
    position: absolute;
    left: 0; top: 1149px;
    width: 1200px; height: 51px;
    background: var(--gold);
    color: var(--ink);
    text-align: center;
    font-weight: 600;
    font-size: 29px;
    line-height: 51px;
  }
</style>
</head>
<body>
  <main class="banner">
    <div class="brand">
      <span class="brand-dot"></span>
      <span class="brand-name">Altair<br>Geosurveys</span>
    </div>

    <h1 class="headline">Exploring Nevada<br>Since 2007</h1>

    <div class="photo photo-snow" role="img" aria-label="Survey helicopter with magnetometer boom flying over snowy rocky mountains"></div>
    <div class="photo photo-valley" role="img" aria-label="Blue survey helicopter flying over green hills with mountains behind"></div>
    <div class="photo photo-lake" role="img" aria-label="Dark grey, orange and white survey helicopter over a turquoise glacial lake"></div>
    <div class="photo photo-sky" role="img" aria-label="Light blue helicopter flying against a deep blue sky"></div>

    <div class="ribbon ribbon-local">Local Company</div>
    <div class="ribbon ribbon-global">Global Expertise</div>

    <section class="service service-em">
      <h2 class="service-title">Electromagnetics</h2>
      <ul class="service-list">
        <li>Frequency Domain</li>
        <li>Time Domain</li>
        <li>Passive</li>
      </ul>
    </section>
    <section class="service service-radio">
      <h2 class="service-title">Radiometric</h2>
      <ul class="service-list">
        <li>256/512 Channels</li>
        <li>Up to 33 Litres</li>
      </ul>
    </section>
    <section class="service service-mag">
      <h2 class="service-title">Magnetics</h2>
      <ul class="service-list">
        <li>Helicopter, Fixed wing, and Drone</li>
        <li>Total field and gradient</li>
      </ul>
    </section>
    <section class="service service-consult">
      <h2 class="service-title">Consulting</h2>
      <ul class="service-list">
        <li>Survey design</li>
        <li>Interpretations</li>
        <li>Inversions</li>
      </ul>
    </section>

    <footer class="footer">www.altairgeosurveys.com</footer>
  </main>
</body>
</html>
```